Zielgruppe
Immobilienmakler
Aufgabenstellung
Top moderne hochwertige Visitenkate, wir hätten gerne eine sehr hochwertig moderne Visitenkarte mit Bild vom Mitarbeiter... Anbei habe ich die alte Visitenkarte die ich sehr kindlich finde... Es sollte jetzt sehr exklusive aussehen. Alle Daten können von der alten Visitenkarte übernommen werden.. danke

```html
<!DOCTYPE html>
<html lang="de">
<head>
<meta charset="utf-8">
<title>Velta Agentur – Visitenkarte</title>
<link rel="stylesheet" href="https://fonts.googleapis.com/css2?family=Ubuntu:wght@400;500&display=swap">
<style>
  :root {
    --brand-green: #1b8a3f;
    --ink: #2b2b2b;
    --card: #ffffff;
    --stage: #e9e9e7;
    --photo-light: #eef1f4;
    --photo-mid: #c9cfd6;
    --tail: #1e1e1e;
  }
  * { box-sizing: border-box; margin: 0; padding: 0; }
  html, body { width: 1200px; height: 764px; overflow: hidden; }
  body {
    background: var(--stage);
    font-family: "Ubuntu", sans-serif;
    color: var(--ink);
    position: relative;
  }
  .card {
    position: absolute;
    top: 290px;
    width: 488px;
    height: 316px;
    background: var(--card);
    box-shadow: 0 2px 8px rgba(0,0,0,0.18);
    overflow: hidden;
  }
  .card--front { left: 88px; }
  .card--back { left: 619px; }

  .side-band {
    position: absolute;
    top: 0; right: 0;
    width: 39px; height: 100%;
    background: var(--brand-green);
  }
  .side-band__url {
    position: absolute;
    left: 50%;
    top: 37px;
    transform-origin: 0 0;
    transform: translate(-9px, 148px) rotate(-90deg);
    color: #fff;
    font-size: 13px;
    white-space: nowrap;
    letter-spacing: 0.2px;
  }

  .company-name {
    position: absolute;
    font-weight: 500;
    color: var(--ink);
    white-space: nowrap;
  }
  .card--front .company-name { left: 62px; top: 176px; font-size: 40px; }
  .card--back .company-name { left: 76px; top: 32px; font-size: 28px; }

  .contact {
    position: absolute;
    left: 160px;
    top: 94px;
    font-size: 13.5px;
    line-height: 17.5px;
  }
  .contact__address { margin-bottom: 11px; }
  .contact__row { display: flex; }
  .contact__label { width: 55px; }

  .portrait {
    position: absolute;
    left: 42px; top: 161px;
    width: 106px; height: 106px;
  }
  .portrait__shape { position: absolute; left: 0; top: 0; overflow: visible; }

  .person {
    position: absolute;
    left: 160px;
    top: 222px;
  }
  .person__name {
    color: var(--brand-green);
    font-size: 18px;
    line-height: 22px;
    margin-bottom: 1px;
  }
  .person__role { font-size: 13.5px; line-height: 17.5px; }
</style>
</head>
<body>

<section class="card card--front">
  <div class="company-name">Velta Agentur</div>
  <div class="side-band"><span class="side-band__url">www.velta-agentur.de</span></div>
</section>

<section class="card card--back">
  <div class="company-name">Velta Agentur</div>

  <div class="contact">
    <p class="contact__address">Am Felsweg 4 · 6850 Dornach</p>
    <p class="contact__row"><span class="contact__label">Telefon</span><span>+43 5572 41 208 30</span></p>
    <p class="contact__row"><span class="contact__label">Mobil</span><span>+43 664 2741 318</span></p>
    <p class="contact__row"><span class="contact__label">E-Mail</span><span>lorenzo@velta-agentur.com</span></p>
  </div>

  <div class="portrait">
    <svg class="portrait__shape" width="106" height="130" viewBox="0 0 106 130">
      <defs>
        <radialGradient id="portrait-fill" cx="50%" cy="40%" r="60%">
          <stop offset="0" stop-color="var(--photo-light)"/>
          <stop offset="1" stop-color="var(--photo-mid)"/>
        </radialGradient>
      </defs>
      <polygon points="24,99 48,105 28,124" fill="var(--tail)"/>
      <circle cx="53" cy="53" r="53" fill="url(#portrait-fill)" role="img" aria-label="Porträtfoto des Mitarbeiters im weißen Hemd"/>
    </svg>
  </div>

  <div class="person">
    <p class="person__name">Lorenzo Albrecht</p>
    <p class="person__role">Dipl. Immobilienmanager</p>
    <p class="person__role">Geschäftsführer</p>
  </div>

  <div class="side-band"><span class="side-band__url">www.velta-agentur.de</span></div>
</section>

</body>
</html>
```